Letterhead, stationery and email signature for construction business

I need the letterhead, stationery and email signature designs for a construction business. I want them to have a corporate feel to them.

I've attached the logo for reference.

```html
<!DOCTYPE html>
<html lang="en">
<head>
<meta charset="utf-8">
<title>Halvorn Builders – Presentation Folder</title>
<link rel="stylesheet" href="https://fonts.googleapis.com/css2?family=Open+Sans:wght@400;600;700&family=Lato:wght@400;700&display=swap">
<style>
  :root {
    --backdrop: #b7b6b8;
    --brand-blue: #3157a0;
    --slate: #6e7389;
    --charcoal: #4c4d5a;
    --paper: #ffffff;
    --ink: #1f1f24;
    --inside-light: #f4f4f4;
    --inside-shade: #bdbdbd;
  }
  * { box-sizing: border-box; margin: 0; padding: 0; }
  html, body { width: 982px; height: 1200px; overflow: hidden; }
  body {
    background: var(--backdrop);
    font-family: "Open Sans", Arial, sans-serif;
    position: relative;
  }
  .spread {
    position: absolute;
    left: 151px;
    width: 680px;
    height: 450px;
    display: flex;
    box-shadow: 0 14px 30px rgba(0,0,0,.25);
  }
  .spread--outside { top: 60px; }
  .spread--inside { top: 620px; }
  .panel { position: relative; width: 340px; height: 450px; overflow: hidden; }

  /* Back cover */
  .back-cover { background: var(--brand-blue); color: var(--paper); }
  .back-cover .brand {
    position: absolute; left: 40px; top: 130px;
    display: flex; align-items: center; gap: 12px;
  }
  .brand-square { width: 34px; height: 34px; background: var(--paper); }
  .brand-name {
    font-weight: 700; font-size: 27px; line-height: 1.05; letter-spacing: 1px;
  }
  .brand-name small { display: block; font-size: 13px; letter-spacing: 8px; }
  .back-cover .address {
    position: absolute; left: 0; right: 0; top: 360px;
    text-align: center; font-size: 11px;
  }
  .back-cover .address::after {
    content: ""; display: block; width: 110px; height: 1px;
    background: var(--paper); margin: 7px auto 0;
  }
  .contact-row {
    position: absolute; left: 20px; right: 10px; top: 400px;
    display: flex; gap: 10px; font-size: 10.5px; align-items: center;
  }
  .contact-row span { display: flex; align-items: center; gap: 4px; }
  .icon { width: 9px; height: 9px; fill: currentColor; }

  /* Front cover */
  .front-cover { background: var(--paper); }
  .mark-area {
    position: absolute; left: 40px; top: 50px; width: 260px; height: 260px;
    background: linear-gradient(135deg, var(--slate), var(--charcoal) 55%, var(--brand-blue) 56%, #2e5fa8);
    display: flex; flex-direction: column; align-items: center; justify-content: center; gap: 14px;
    color: var(--paper);
  }
  .mark-area .brand-square { width: 40px; height: 40px; }
  .mark-area .brand-name { font-size: 26px; text-align: center; }
  .front-cover .stripe-dark {
    position: absolute; left: 0; right: 0; bottom: 26px; height: 3px; background: var(--charcoal);
  }
  .front-cover .stripe-blue {
    position: absolute; left: 0; right: 0; bottom: 0; height: 20px; background: var(--brand-blue);
  }

  /* Inside left */
  .inside-left {
    background: linear-gradient(90deg, var(--paper), var(--inside-light) 40%, var(--inside-shade));
  }
  .pocket-left {
    position: absolute; left: 0; bottom: 0; width: 340px; height: 130px;
    background: var(--brand-blue);
    border-top-right-radius: 26px;
  }

  /* Inside right */
  .inside-right {
    background: linear-gradient(90deg, var(--inside-shade), #e6e6e6 20%, var(--paper));
  }
  .letterhead {
    position: absolute; left: 22px; top: 18px; width: 300px; height: 400px;
    background: var(--paper); color: var(--ink);
    box-shadow: -3px 3px 10px rgba(0,0,0,.2);
    font-family: "Lato", Arial, sans-serif;
    padding: 20px 18px;
  }
  .letterhead-header {
    display: flex; justify-content: space-between; align-items: center;
    padding-bottom: 10px; border-bottom: 1px solid var(--brand-blue);
  }
  .letterhead .brand { display: flex; align-items: center; gap: 6px; color: var(--brand-blue); }
  .letterhead .brand-square { width: 18px; height: 18px; background: var(--brand-blue); }
  .letterhead .brand-name { font-family: "Open Sans", Arial, sans-serif; font-size: 14px; }
  .letterhead .brand-name small { font-size: 7px; letter-spacing: 4px; }
  .letterhead-contact {
    border-left: 1px solid var(--brand-blue); padding-left: 8px;
    font-size: 6.5px; line-height: 1.45; color: #444;
  }
  .letterhead-contact .icon { width: 6px; height: 6px; fill: var(--brand-blue); margin-right: 2px; vertical-align: middle; }
  .letter-body { font-size: 6.3px; line-height: 1.4; margin-top: 14px; }
  .letter-body p { margin-bottom: 7px; }
  .letter-body .salutation { font-size: 8px; font-weight: 700; margin-bottom: 5px; }
  .pocket-right {
    position: absolute; left: 0; bottom: 0; width: 340px; height: 150px;
    background: var(--slate);
    border-top-left-radius: 26px;
  }
</style>
</head>
<body>
  <section class="spread spread--outside">
    <div class="panel back-cover">
      <div class="brand">
        <div class="brand-square"></div>
        <div class="brand-name">HALVORN<small>BUILDERS</small></div>
      </div>
      <p class="address">Your address, City State, Zip 1234</p>
      <div class="contact-row">
        <span><svg class="icon" viewBox="0 0 10 10"><path d="M1 3c0-1 1-2 2-2h4c1 0 2 1 2 2v1H7V3H3v1H1zM2 5h6l1 4H1z"/></svg>123 456 789</span>
        <span><svg class="icon" viewBox="0 0 10 10"><path d="M0 2h10v6H0zM0 2l5 3 5-3"/></svg>info@yourgmail.com</span>
        <span><svg class="icon" viewBox="0 0 10 10"><circle cx="5" cy="5" r="4.5"/></svg>www.yourwebsite.com</span>
      </div>
    </div>
    <div class="panel front-cover">
      <div class="mark-area" role="img" aria-label="Large brand emblem area in slate and blue">
        <div class="brand-square"></div>
        <div class="brand-name">HALVORN<small>BUILDERS</small></div>
      </div>
      <div class="stripe-dark"></div>
      <div class="stripe-blue"></div>
    </div>
  </section>

  <section class="spread spread--inside">
    <div class="panel inside-left">
      <div class="pocket-left"></div>
    </div>
    <div class="panel inside-right">
      <article class="letterhead">
        <header class="letterhead-header">
          <div class="brand">
            <div class="brand-square"></div>
            <div class="brand-name">HALVORN<small>BUILDERS</small></div>
          </div>
          <div class="letterhead-contact">
            Your address, City<br>State, Zip 1234<br>
            <svg class="icon" viewBox="0 0 10 10"><path d="M1 3c0-1 1-2 2-2h4c1 0 2 1 2 2v1H7V3H3v1H1zM2 5h6l1 4H1z"/></svg>123 456 789<br>
            <svg class="icon" viewBox="0 0 10 10"><path d="M0 2h10v6H0z"/></svg>info@yourgmail.com<br>
            <svg class="icon" viewBox="0 0 10 10"><circle cx="5" cy="5" r="4.5"/></svg>www.yourwebsite.com
          </div>
        </header>
        <div class="letter-body">
          <p>January-03-2020</p>
          <p>Mr, John Doe<br>President</p>
          <p>Marlow Corporation<br>123 Street Name, Suite# 10<br>City, State, 120023</p>
          <p class="salutation">Dear Mr, John</p>
          <p>Lorem ipsum dolor sit amet, consectetur adipiscing elit, sed do eiusmod tempor incididunt ut labore et dolore magna aliqua. Ut enim ad minim veniam, quis nostrud exercitation ullamco laboris nisi ut aliquip ex ea commodo consequat. Duis aute irure dolor in reprehenderit in voluptate velit esse cillum dolore eu fugiat nulla pariatur.</p>
          <p>Lorem ipsum dolor sit amet, consectetur adipiscing elit, sed do eiusmod tempor incididunt ut labore et dolore magna aliqua. Ut enim ad minim veniam, quis nostrud exercitation ullamco laboris nisi ut aliquip ex ea commodo consequat.</p>
        </div>
      </article>
      <div class="pocket-right"></div>
    </div>
  </section>
</body>
</html>
```